Kestrel Home Business Card Design

We need a business card for a Building company based in Queensland, Australia. Our colours are orange black and we do base all our homes design names and other aspect of our business on astrology. We want the consumer to perceive the company as professional and to attract investors to our company.We have over 20 years in the building industry.We pride ourselves on our innovation of designs and making the building process for anyone from families to investor a smooth and simple experience.
Business
Amelia Prichard0411752116PO Box 454, Mudgeerbaameliaprichard@zodiachomes.com

```html
<!DOCTYPE html>
<html lang="en">
<head>
<meta charset="utf-8">
<title>Kestrel Homes – Business Card</title>
<link rel="stylesheet" href="https://fonts.googleapis.com/css2?family=Open+Sans:wght@400;600;700&display=swap">
<style>
  :root {
    --backdrop: #3b342f;
    --card: #1b1b1b;
    --card-edge: #111111;
    --ink: #f2f2f2;
    --ink-soft: #d8d8d8;
    --accent: #f39a1e;
    --silver: #d9d9d9;
    --divider: #4a4a4a;
  }
  * { box-sizing: border-box; margin: 0; padding: 0; }
  html, body {
    width: 1200px; height: 844px; overflow: hidden;
    background: var(--backdrop);
    font-family: "Open Sans", Arial, sans-serif;
  }
  .stage {
    position: relative; width: 1200px; height: 844px;
    display: flex; align-items: center; justify-content: center; gap: 40px;
  }
  .card {
    position: relative; width: 525px; height: 300px;
    background: var(--card);
    border: 1px solid var(--card-edge);
    box-shadow: 0 14px 30px rgba(0,0,0,.45);
  }
  /* Front */
  .brand {
    position: absolute; top: 26px; left: 0; width: 100%;
    display: flex; flex-direction: column; align-items: center; gap: 8px;
  }
  .brand-dot {
    width: 46px; height: 46px; border-radius: 50%;
    background: var(--accent);
  }
  .brand-name {
    font-weight: 700; font-size: 28px; color: var(--ink); line-height: 1.1;
  }
  .details {
    position: absolute; top: 140px; left: 20px; right: 16px;
    display: flex; align-items: flex-start;
  }
  .person {
    width: 220px; text-align: right; padding-right: 14px;
    border-right: 1px solid var(--divider);
    padding-bottom: 6px;
  }
  .person-name { font-size: 19px; font-weight: 700; color: var(--ink); line-height: 1.2; }
  .person-role { font-size: 14px; color: var(--accent); line-height: 1.3; margin-bottom: 8px; }
  .person-address { font-size: 13.5px; color: var(--ink-soft); line-height: 1.35; }
  .contacts { list-style: none; padding-left: 14px; }
  .contact {
    display: flex; align-items: center; gap: 9px;
    font-size: 12px; color: var(--ink-soft); height: 26px; white-space: nowrap;
  }
  .contact-icon {
    width: 18px; height: 18px; flex: none; border-radius: 2px;
    background: var(--accent);
    display: flex; align-items: center; justify-content: center;
  }
  /* Back */
  .card-back { display: flex; align-items: center; justify-content: center; }
  .back-name {
    font-weight: 700; font-size: 48px; color: var(--silver); letter-spacing: 1px;
  }
</style>
</head>
<body>
<main class="stage">
  <section class="card card-front">
    <div class="brand">
      <span class="brand-dot"></span>
      <span class="brand-name">Kestrel Homes</span>
    </div>
    <div class="details">
      <div class="person">
        <p class="person-name">Harriet Colvane</p>
        <p class="person-role">Managing Director</p>
        <p class="person-address">PO Box 000, Starfall Vale<br>Queensland, Australia</p>
      </div>
      <ul class="contacts">
        <li class="contact">
          <span class="contact-icon"><svg width="12" height="12" viewBox="0 0 12 12"><path d="M2.5 1h2l1 2.5-1.3 1a6 6 0 0 0 3.3 3.3l1-1.3L11 7.5v2a1 1 0 0 1-1 1A9 9 0 0 1 1.5 2a1 1 0 0 1 1-1z" fill="#fff"/></svg></span>
          0491 570 156
        </li>
        <li class="contact">
          <span class="contact-icon"><svg width="12" height="12" viewBox="0 0 12 12"><rect x="3" y="1" width="6" height="10" rx="1" fill="none" stroke="#fff" stroke-width="1.3"/><circle cx="6" cy="9" r=".7" fill="#fff"/></svg></span>
          07 5550 4187
        </li>
        <li class="contact">
          <span class="contact-icon"><svg width="12" height="12" viewBox="0 0 12 12"><rect x="1" y="2.5" width="10" height="7" fill="none" stroke="#fff" stroke-width="1.2"/><path d="M1 2.5l5 4 5-4" fill="none" stroke="#fff" stroke-width="1.2"/></svg></span>
          harrietcolvane@kestrelhomes.example
        </li>
        <li class="contact">
          <span class="contact-icon"><svg width="12" height="12" viewBox="0 0 12 12"><path d="M5 7l2-2M4.5 5.5L3 7a1.8 1.8 0 0 0 2.5 2.5L7 8M7.5 6.5L9 5a1.8 1.8 0 0 0-2.5-2.5L5 4" fill="none" stroke="#fff" stroke-width="1.3" stroke-linecap="round"/></svg></span>
          www.kestrelhomes.example
        </li>
      </ul>
    </div>
  </section>
  <section class="card card-back">
    <span class="back-name">Kestrel Homes</span>
  </section>
</main>
</body>
</html>
```